Walk Beside The River

Business Card design

Target Market(s)

People who require support in the commnity

Industry/Entity Type

Mental Health Support

Contact Information for Business Card

Mental Health Support Rosalind Tavener walkbesidetheriver@mailcove.com.au 0481 637 092 PO Box 926 Tallowbrook NSW 2491

Colors
6B429C
8869AF
B7A5CE
E3DAEB
F3F0F8

Requirements
Must have
• Logo & details listed above
Should not have
• No red or orange

```html
<!DOCTYPE html>
<html lang="en">
<head>
<meta charset="utf-8">
<title>Walk Beside The River – Business Card</title>
<link rel="stylesheet" href="https://fonts.googleapis.com/css2?family=Open+Sans:wght@400;600;700&display=swap">
<style>
  :root {
    --stage: #2a292e;
    --card: #1e1d22;
    --card-edge: #f2ea2a;
    --accent-yellow: #f2ea2a;
    --olive: #403e2d;
    --olive-soft: rgba(64, 62, 45, 0);
    --purple: #6b429c;
    --text-light: #f3f0f8;
    --pattern-light: #6d6c72;
    --pattern-dark: #1e1d22;
  }
  * { box-sizing: border-box; margin: 0; padding: 0; }
  html, body { width: 1200px; height: 780px; overflow: hidden; }
  body {
    background: var(--stage);
    font-family: "Open Sans", Arial, sans-serif;
    position: relative;
  }
  .card {
    position: absolute;
    width: 540px;
    height: 320px;
    top: 230px;
    background: var(--card);
    border-radius: 22px;
    border: 3px solid var(--card-edge);
    overflow: hidden;
  }
  .card--back { left: 40px; }
  .card--front { left: 620px; }

  .back-pattern {
    position: absolute;
    inset: 0;
    background: linear-gradient(200deg, var(--pattern-light) 0%, #3a393f 25%, var(--pattern-dark) 50%);
  }

  .star-decoration {
    position: absolute;
    right: -60px;
    top: -90px;
    width: 360px;
    height: 330px;
    background: radial-gradient(ellipse at 60% 45%, var(--olive) 0%, var(--olive) 35%, var(--olive-soft) 70%);
  }
  .person {
    position: absolute;
    right: 56px;
    top: 28px;
    text-align: right;
  }
  .person-name {
    font-size: 27px;
    font-weight: 700;
    color: var(--accent-yellow);
    line-height: 1.1;
  }
  .person-role {
    font-size: 14px;
    color: var(--text-light);
    margin-top: 4px;
  }
  .person-bar {
    position: absolute;
    right: 22px;
    top: 24px;
    width: 22px;
    height: 44px;
    background: var(--purple);
  }

  .brand {
    position: absolute;
    left: 32px;
    top: 92px;
    display: flex;
    align-items: center;
    gap: 14px;
  }
  .brand-dot {
    width: 72px;
    height: 72px;
    border-radius: 50%;
    background: var(--purple);
    flex: none;
  }
  .brand-name {
    font-size: 15px;
    font-weight: 600;
    color: var(--text-light);
    white-space: nowrap;
  }

  .service {
    position: absolute;
    left: 118px;
    top: 168px;
    color: var(--text-light);
    font-size: 16px;
    line-height: 1.35;
  }

  .contacts {
    position: absolute;
    left: 32px;
    bottom: 22px;
    list-style: none;
    color: var(--text-light);
    font-size: 15px;
    line-height: 1.55;
  }
  .contacts li { display: flex; align-items: center; gap: 10px; }
  .contacts svg { width: 16px; height: 16px; flex: none; }
</style>
</head>
<body>

  <section class="card card--back" aria-label="Card back">
    <div class="back-pattern" role="img" aria-label="Repeating star pattern fading from silver to black"></div>
  </section>

  <section class="card card--front" aria-label="Card front">
    <div class="star-decoration" role="img" aria-label="Large olive star decoration"></div>
    <div class="person-bar"></div>
    <div class="person">
      <p class="person-name">Mirela Havranova</p>
      <p class="person-role">CEO/Director</p>
    </div>

    <div class="brand">
      <span class="brand-dot"></span>
      <span class="brand-name">Walk Beside The River</span>
    </div>

    <div class="service">
      <p>Mental Health Support</p>
      <p>Rosalind Tavener</p>
    </div>

    <ul class="contacts">
      <li>
        <svg viewBox="0 0 24 24" fill="none" stroke="var(--accent-yellow)" stroke-width="2.2" stroke-linecap="round"><path d="M5 3h4l2 5-2.5 1.5a11 11 0 0 0 6 6L16 13l5 2v4a2 2 0 0 1-2 2A17 17 0 0 1 3 5a2 2 0 0 1 2-2z"/></svg>
        0481 637 092
      </li>
      <li>
        <svg viewBox="0 0 24 24" fill="none" stroke="var(--accent-yellow)" stroke-width="2.2" stroke-linejoin="round"><rect x="3" y="5" width="18" height="14" rx="2"/><path d="M3 7l9 6 9-6"/></svg>
        walkbesidetheriver@mailcove.com.au
      </li>
      <li>
        <svg viewBox="0 0 24 24" fill="none" stroke="var(--accent-yellow)" stroke-width="2.2"><path d="M12 22s7-7 7-12a7 7 0 0 0-14 0c0 5 7 12 7 12z"/><circle cx="12" cy="10" r="2.5"/></svg>
        PO Box 926 Tallowbrook NSW 2491
      </li>
    </ul>
  </section>

</body>
</html>
```